The K7 Momentum Collective Website

We have a pitch deck and messaging drafted. Target audience is academic institutions and VC investors that have seed money in start ups.

Need a basic website

Industry/Entity Type

LIfe Science, Diagnostic, medical device.

Coding

Coded - Design and coding required

Number of Pages Required

5+ page

```html
<!DOCTYPE html>
<html lang="en">
<head>
<meta charset="utf-8">
<title>The K7 Momentum Collective</title>
<link href="https://fonts.googleapis.com/css2?family=Poppins:wght@300;400;500;600;700&display=swap" rel="stylesheet">
<style>
:root{
  --blue:#0f5cb8;
  --blue-deep:#0a4a98;
  --ink:#1f1f1f;
  --body:#3c3c3c;
  --muted:#8a8a8a;
  --btn-gray:#7b7b7b;
  --line:#d7d7d7;
  --soft:#ececee;
  --footer:#1d1e21;
  --footer-bar:#151618;
  --white:#ffffff;
}
*{box-sizing:border-box;margin:0;padding:0}
html,body{width:1200px;height:5217px;overflow:hidden}
body{font-family:"Poppins",sans-serif;color:var(--ink);background:var(--white);position:relative}
section,header,footer{position:relative;width:1200px;overflow:hidden}
.abs{position:absolute}
.btn{position:absolute;display:flex;align-items:center;justify-content:center;font-weight:600;font-size:15px;letter-spacing:.3px;color:var(--white);text-transform:uppercase}
.btn-gray{background:var(--btn-gray)}
.accent{color:var(--blue)}

/* header */
.site-header{height:110px;background:var(--white)}
.brand{position:absolute;left:75px;top:24px;display:flex;align-items:center;gap:10px}
.brand-dot{width:40px;height:40px;border-radius:50%;background:var(--blue)}
.brand-name{font-size:12.5px;font-weight:600;color:var(--blue);line-height:1.3;text-transform:uppercase;letter-spacing:.2px}
.main-nav a{position:absolute;top:49px;font-size:12.5px;font-weight:500;color:var(--ink);text-decoration:none;letter-spacing:.3px}
.main-nav a.active{color:var(--blue)}
.main-nav a.active::after{content:"";position:absolute;left:0;right:0;bottom:-8px;height:2px;background:var(--blue)}

/* hero */
.hero{height:598px}
.hero-photo{position:absolute;inset:0;background:linear-gradient(120deg,#1d2a3d 0%,#2f4661 35%,#3b5470 55%,#22324a 80%,#1a2535 100%)}
.hero-shade{position:absolute;inset:0;background:rgba(10,20,40,.35)}
.hero-title{position:absolute;top:176px;width:100%;text-align:center;font-size:50px;font-weight:700;color:var(--white);letter-spacing:.5px}
.hero-sub{position:absolute;top:246px;width:100%;text-align:center;font-size:31px;font-weight:300;color:var(--white);letter-spacing:1px}
.hero .btn{left:507px;top:306px;width:186px;height:54px;background:var(--blue);font-size:15px}
.hero-dots{position:absolute;top:548px;left:565px;display:flex;gap:12px}
.hero-dots span{width:9px;height:9px;border-radius:50%;background:var(--white);opacity:.9}
.hero-dots span:first-child{opacity:.5}

/* welcome */
.welcome{height:559px}
.section-title{position:absolute;width:100%;text-align:center;font-weight:700;text-transform:uppercase;letter-spacing:.5px}
.welcome .section-title{top:70px;font-size:36px}
.welcome-lead{position:absolute;top:134px;left:105px;width:990px;text-align:center;font-size:15.5px;line-height:32px;color:var(--body)}
.pillar{position:absolute;top:231px;width:241px;height:245px;border:1.5px solid #8fb2de;padding:26px 14px 0 14px}
.pillar svg{display:block;width:34px;height:34px}
.pillar h3{margin-top:16px;font-size:21px;font-weight:700;color:var(--blue);letter-spacing:.3px}
.pillar p{margin-top:10px;font-size:14px;line-height:27px;color:var(--body)}

/* services */
.services{height:682px;background:var(--blue)}
.services-bg{position:absolute;inset:0;background:linear-gradient(160deg,rgba(255,255,255,.05),rgba(0,0,0,.08))}
.services .section-title{top:62px;font-size:34px;color:var(--white)}
.services-sub{position:absolute;top:122px;width:100%;text-align:center;font-size:20px;font-weight:300;color:var(--white)}
.service-icon{position:absolute;width:70px;height:70px}
.service-text{position:absolute;width:405px;font-size:16px;line-height:28px;color:var(--white);font-weight:300}
.services .btn{left:509px;top:549px;width:181px;height:59px;border:2px solid var(--white)}

/* about */
.about{height:671px}
.about-block{position:absolute;left:0;top:78px;width:434px;height:537px;background:var(--blue)}
.about-photo{position:absolute;left:75px;top:1px;width:513px;height:537px;background:linear-gradient(135deg,#c9d3dc 0%,#7f8c99 40%,#3b4756 75%,#2a3340 100%)}
.about-box{position:absolute;left:497px;top:78px;width:628px;height:535px;border:2px solid var(--line)}
.about h2{position:absolute;left:628px;top:143px;font-size:36px;font-weight:700;text-transform:uppercase;letter-spacing:.3px}
.about-text{position:absolute;left:628px;top:200px;width:470px;font-size:15px;line-height:31px;color:var(--body)}
.about .btn{left:628px;top:479px;width:183px;height:59px}

/* partners */
.partners{height:831px}
.partners-band{position:absolute;left:0;top:26px;width:1200px;height:422px;background:var(--soft)}
.partners .section-title{top:88px;font-size:36px}
.partner{position:absolute;top:174px;width:329px;height:544px;background:var(--white);box-shadow:0 2px 10px rgba(0,0,0,.12);text-align:center}
.partner-photo{width:186px;height:186px;border-radius:50%;margin:27px auto 0;background:radial-gradient(circle at 50% 40%,#b9a492 0%,#6d6a68 55%,#3f4752 100%)}
.partner h3{margin-top:26px;font-size:22px;font-weight:700;color:var(--blue);text-transform:uppercase}
.partner .role{margin-top:4px;font-size:15px;color:var(--muted)}
.partner p{margin:8px 22px 0;font-size:14px;line-height:28px;color:var(--body)}
.partner .btn{top:517px;left:74px;width:181px;height:57px}

/* plan */
.plan{height:574px;background:var(--blue)}
.plan .section-title{top:72px;font-size:34px;color:var(--white)}
.plan-card{position:absolute;top:142px;width:329px;height:357px;background:var(--white);text-align:center}
.plan-card svg{display:block;margin:15px auto 0;width:124px;height:124px}
.plan-card h3{margin-top:8px;font-size:22px;font-weight:700;color:var(--blue);text-transform:uppercase}
.plan-card p{margin:8px 22px 0;font-size:14px;line-height:28px;color:var(--body)}
.plan-arrow{position:absolute;top:302px;width:26px;height:40px}

/* solution */
.solution{height:703px}
.solution-block{position:absolute;left:766px;top:79px;width:434px;height:533px;background:var(--blue)}
.solution-photo{position:absolute;left:614px;top:0;width:511px;height:537px;background:linear-gradient(140deg,#7d8b92 0%,#c6b9a4 35%,#8a6f5d 65%,#4a5563 100%)}
.solution-box{position:absolute;left:75px;top:79px;width:628px;height:533px;border:2px solid var(--line)}
.solution h2{position:absolute;left:105px;top:110px;font-size:36px;font-weight:700;text-transform:uppercase}
.solution-text{position:absolute;left:105px;top:166px;width:470px;font-size:15px;line-height:31px;color:var(--body)}
.solution-text p+p{margin-top:8px}
.solution .btn{left:105px;top:508px;width:181px;height:61px}

/* footer */
.site-footer{height:395px;background:var(--footer);color:#c9c9c9}
.footer-brand{position:absolute;left:75px;top:76px;display:flex;align-items:center;gap:10px}
.footer-brand .brand-dot{width:44px;height:44px}
.footer-brand .brand-name{font-size:13px}
.footer-about{position:absolute;left:75px;top:202px;width:240px;font-size:14px;line-height:28.5px;color:#b7b7b7}
.footer-col{position:absolute;top:76px}
.footer-col h4{font-size:17px;font-weight:600;color:var(--white);text-transform:uppercase;letter-spacing:.5px;margin-bottom:12px}
.footer-col li{list-style:none;font-size:14px;line-height:35px;color:#c2c2c2}
.contact-row{display:flex;gap:14px;font-size:14px;line-height:26px;color:#c2c2c2;margin-bottom:8px}
.contact-row svg{flex:none;width:16px;height:16px;margin-top:5px}
.social{display:flex;gap:16px;margin-top:14px}
.social span{width:18px;height:18px;border-radius:3px;background:var(--white)}
.footer-bar{height:95px;background:var(--footer-bar);display:flex;align-items:center;justify-content:center;font-size:13px;color:#d0d0d0}
</style>
</head>
<body>

<header class="site-header">
  <div class="brand">
    <span class="brand-dot"></span>
    <span class="brand-name">The K7 Momentum<br>Collective</span>
  </div>
  <nav class="main-nav">
    <a class="active" style="left:444px">HOME</a>
    <a style="left:521px">ABOUT US</a>
    <a style="left:624px">SERVICES</a>
    <a style="left:724px">OUR PARTNERS</a>
    <a style="left:857px">SOLUTIONS</a>
    <a style="left:969px">BLOG</a>
    <a style="left:1042px">CONTACT US</a>
  </nav>
</header>

<section class="hero">
  <div class="hero-photo" role="img" aria-label="Business team meeting in a modern office with a presenter beside a large analytics dashboard screen"></div>
  <div class="hero-shade"></div>
  <h1 class="hero-title">THE K7 MOMENTUM COLLECTIVE™</h1>
  <p class="hero-sub">Accelerating your innovative IP to market</p>
  <a class="btn">Read More</a>
  <div class="hero-dots"><span></span><span></span><span></span><span></span></div>
</section>

<section class="welcome">
  <h2 class="section-title">Welcome to <span class="accent">The K7 Momentum Collective</span></h2>
  <p class="welcome-lead">The K7 Momentum Collective™ (K7) rapidly brings innovative and transformational IP to market by assisting with all elements of a company’s development.</p>
  <div class="pillar" style="left:75px">
    <svg viewBox="0 0 34 34"><circle cx="17" cy="17" r="15.5" fill="none" stroke="#666" stroke-width="2"/><path d="M10 17.5l5 5 9-10" fill="none" stroke="#666" stroke-width="2.2"/></svg>
    <h3>WE ARE...</h3>
    <p>experienced in strategic business planning and execution, and operational excellence.</p>
  </div>
  <div class="pillar" style="left:345px">
    <svg viewBox="0 0 34 34"><circle cx="17" cy="17" r="15.5" fill="none" stroke="#666" stroke-width="2"/><path d="M10 17.5l5 5 9-10" fill="none" stroke="#666" stroke-width="2.2"/></svg>
    <h3>WE HAVE...</h3>
    <p>100 years of collective experiences and vast network of people, partners, and processes.</p>
  </div>
  <div class="pillar" style="left:615px">
    <svg viewBox="0 0 34 34"><circle cx="17" cy="17" r="15.5" fill="none" stroke="#666" stroke-width="2"/><path d="M10 17.5l5 5 9-10" fill="none" stroke="#666" stroke-width="2.2"/></svg>
    <h3>WE CAN...</h3>
    <p>serve as the initial executive team to ensure strategic alignment with a focus on marketplace.</p>
  </div>
  <div class="pillar" style="left:885px">
    <svg viewBox="0 0 34 34"><circle cx="17" cy="17" r="15.5" fill="none" stroke="#666" stroke-width="2"/><path d="M10 17.5l5 5 9-10" fill="none" stroke="#666" stroke-width="2.2"/></svg>
    <h3>WE WILL...</h3>
    <p>remove the uncertainty and confusion common in the initial stages of a company’s formation.</p>
  </div>
</section>

<section class="services">
  <div class="services-bg"></div>
  <h2 class="section-title">Our Services</h2>
  <p class="services-sub">This includes the following services</p>

  <svg class="service-icon" style="left:85px;top:200px" viewBox="0 0 70 70" fill="none" stroke="#fff" stroke-width="4">
    <path d="M16 6h26l14 14v44H16z"/><path d="M42 6v14h14"/><path d="M26 34h20M26 44h20M26 54h14"/>
  </svg>
  <p class="service-text" style="left:180px;top:199px">Reading/reviewing business plans and pitch decks, which may include the inventor disclosure(s), provisional patent(s), and inventor interview.</p>

  <svg class="service-icon" style="left:624px;top:196px" viewBox="0 0 70 70" fill="none" stroke="#fff" stroke-width="5">
    <path d="M12 32a22 22 0 0 1 40-12"/><path d="M54 8v14H40"/><path d="M58 38a22 22 0 0 1-40 12"/><path d="M16 62V48h14"/>
  </svg>
  <p class="service-text" style="left:722px;top:199px">Working in a strategic capacity with existing portfolio companies as either a coach/mentor role or as a fractional executive team member as needed.</p>

  <svg class="service-icon" style="left:82px;top:362px" viewBox="0 0 70 70" fill="#fff">
    <rect x="4" y="8" width="5" height="54"/><rect x="4" y="57" width="62" height="5"/><rect x="17" y="34" width="7" height="20"/><rect x="30" y="22" width="7" height="32"/><rect x="43" y="30" width="7" height="24"/><rect x="56" y="16" width="7" height="38"/>
  </svg>
  <p class="service-text" style="left:180px;top:363px">Assessing market/company attractiveness through identification of product definition and target market segments, as well as a competitor analysis to help identify potential revenue growth and traction.</p>

  <svg class="service-icon" style="left:624px;top:358px" viewBox="0 0 70 70" fill="none" stroke="#fff" stroke-width="5">
    <path d="M6 8v56h58"/><path d="M14 50l14-16 10 10 20-22"/><path d="M46 20h14v14"/>
  </svg>
  <p class="service-text" style="left:722px;top:363px">Preparing market analyses and presentations to assist with investment decisions and for engagement with the firm's extensive network of corporate relationships.</p>

  <a class="btn">Read More</a>
</section>

<section class="about">
  <div class="about-block"></div>
  <div class="about-photo" role="img" aria-label="Smiling businessman in a suit in conversation with colleagues"></div>
  <div class="about-box"></div>
  <h2>About <span class="accent">The Company</span></h2>
  <p class="about-text">The K7 Momentum Collective (K7) is a group of experienced executives whose careers have been focused on taking innovative ideas to market by strategically navigating the buildout of best-in-class life science and diagnostic organizations.<br>This experience makes us uniquely equipped to be involved in all aspects of your due diligence on new or existing investments.</p>
  <a class="btn btn-gray">Read More</a>
</section>

<section class="partners">
  <div class="partners-band"></div>
  <h2 class="section-title">Meet <span class="accent">The Partners</span></h2>
  <div class="partner" style="left:75px">
    <div class="partner-photo" role="img" aria-label="Portrait of partner Brandt Keller"></div>
    <h3>Brandt Keller</h3>
    <div class="role">Partner</div>
    <p>Marketing, Commercial Development, Product Development, Growth Strategy 30+ years of marketing, sales, product development, and operations executive leader in the life science and diagnostic industries.</p>
    <a class="btn btn-gray">Read More</a>
  </div>
  <div class="partner" style="left:436px">
    <div class="partner-photo" role="img" aria-label="Portrait of partner Sofia Brennan"></div>
    <h3>Sofia Brennan</h3>
    <div class="role">Partner</div>
    <p>Regulatory, Quality, Product Development, Operations 30+ years working in diagnostic and medical device area with focus on creative solutions to bring product to market.</p>
    <a class="btn btn-gray">Read More</a>
  </div>
  <div class="partner" style="left:797px">
    <div class="partner-photo" role="img" aria-label="Portrait of partner Jonas Talbot"></div>
    <h3>Jonas Talbot</h3>
    <div class="role">Partner</div>
    <p>Board Development, Funding, Back-office Set-up, Operations 30+ years accomplished CEO and well-rounded executive with more than 25 years of experience in medical devices, research tools and diagnostics.</p>
    <a class="btn btn-gray">Read More</a>
  </div>
</section>

<section class="plan">
  <h2 class="section-title">K7 Plan Elements</h2>
  <svg class="plan-arrow" style="left:38px" viewBox="0 0 26 40" fill="none" stroke="#fff" stroke-width="3"><path d="M20 4L6 20l14 16"/></svg>
  <svg class="plan-arrow" style="left:1136px" viewBox="0 0 26 40" fill="none" stroke="#fff" stroke-width="3"><path d="M6 4l14 16L6 36"/></svg>

  <div class="plan-card" style="left:75px">
    <svg viewBox="0 0 124 124" fill="none"><circle cx="62" cy="62" r="56" stroke="#0f5cb8" stroke-width="4"/><circle cx="62" cy="50" r="12" stroke="#777" stroke-width="3"/><path d="M38 84c2-14 12-20 24-20s22 6 24 20z" stroke="#777" stroke-width="3"/></svg>
    <h3>Executive Summary</h3>
    <p>Articulates a brief snapshot of the business model/plan, including name, location, products or services, mission statement.</p>
  </div>
  <div class="plan-card" style="left:436px">
    <svg viewBox="0 0 124 124" fill="none"><circle cx="62" cy="62" r="56" stroke="#0f5cb8" stroke-width="4"/><rect x="46" y="36" width="32" height="52" stroke="#777" stroke-width="3"/><path d="M54 46h4M66 46h4M54 56h4M66 56h4M54 66h4M66 66h4M58 88v-10h8v10" stroke="#777" stroke-width="3"/></svg>
    <h3>Company Description</h3>
    <p>Describes a high-level view of the business nature, customer need being met, history, legality, short term, and long-term goals.</p>
  </div>
  <div class="plan-card" style="left:797px">
    <svg viewBox="0 0 124 124" fill="none"><circle cx="62" cy="62" r="56" stroke="#0f5cb8" stroke-width="4"/><rect x="42" y="40" width="40" height="28" stroke="#777" stroke-width="3"/><path d="M34 76h56l-4 8H38z" stroke="#777" stroke-width="3"/></svg>
    <h3>Products/Services</h3>
    <p>Provides a description of the product/services, its competitive advantages, customer benefits, reimbursement, estimated supplier costs.</p>
  </div>
</section>

<section class="solution">
  <div class="solution-block"></div>
  <div class="solution-photo" role="img" aria-label="Several hands joining colourful jigsaw puzzle pieces with business icons"></div>
  <div class="solution-box"></div>
  <h2>The <span class="accent">Solution</span></h2>
  <div class="solution-text">
    <p>K7 was started to solve significant problems associated with rapidly bringing innovative and transformational IP to market.</p>
    <p>These costly problems include:<br>Incomplete strategic planning,&nbsp; Difficulty finding leadership,&nbsp; Not able to differentiate a product or service from others that are already available, and Ignoring the needs of customer.<br>(Capital shortages, poor locations, and scaling too soon can also cause a start-up to have problems.)</p>
  </div>
  <a class="btn btn-gray">Read More</a>
</section>

<footer class="site-footer">
  <div class="footer-brand">
    <span class="brand-dot"></span>
    <span class="brand-name">The K7 Momentum<br>Collective</span>
  </div>
  <p class="footer-about">The K7 Momentum Collective (K7) is a group of experienced executives whose careers have been focused on taking innovative ideas to market by strategically..</p>

  <div class="footer-col" style="left:377px">
    <h4>Company</h4>
    <ul><li>Home</li><li>About Us</li><li>Services</li><li>Our Partners</li><li>Solutions</li><li>Blog</li><li>Contact Us</li></ul>
  </div>
  <div class="footer-col" style="left:598px">
    <h4>Resources</h4>
    <ul><li>Sed ut perspiciatis</li><li>Unde omnis iste</li><li>Natus error sit voluptate</li><li>Accusantium</li><li>Doloremque lauda</li></ul>
  </div>
  <div class="footer-col" style="left:886px;width:260px">
    <h4>Contact Info</h4>
    <div class="contact-row"><svg viewBox="0 0 16 16" fill="#3a8fe8"><path d="M8 1a5 5 0 0 0-5 5c0 4 5 9 5 9s5-5 5-9a5 5 0 0 0-5-5zm0 7a2 2 0 1 1 0-4 2 2 0 0 1 0 4z"/></svg><span>4120 Harbor Mesa Road<br>Carlsbad, CA 92010</span></div>
    <div class="contact-row"><svg viewBox="0 0 16 16" fill="#3a8fe8"><path d="M3 1l3 3-2 2c1 2 3 4 5 5l2-2 3 3-2 3C7 15 1 9 1 3z"/></svg><span>+1 555-014-2270</span></div>
    <div class="contact-row"><svg viewBox="0 0 16 16" fill="#3a8fe8"><path d="M1 3h14v10H1z"/><path d="M1 3l7 6 7-6" stroke="#1d1e21" stroke-width="1.4" fill="none"/></svg><span>hello@k7momentum.example</span></div>
    <div class="social"><span></span><span></span><span></span><span></span><span></span></div>
  </div>
</footer>

<div class="footer-bar">Copyright ©2023 &nbsp;K7 Momentum Collective .All Right Reserved</div>

</body>
</html>
```